VORTEQ

It’s is a startup business. We design and build new products.

Target Market(s)

For my first two products, they are targeting the laundry market, hanger accessory, and new modern style clothes dryer. I also have a Pet Treat product at patent stage, and there are other products not yet started but will be more engineering based. Therefore from young adults to older population

Industry/Entity Type

Colours of website to match the logo (att)

Coding

Coded - Design and coding required

Number of Pages Required

1 page

Font styles to use
Other font styles liked:
• Some of the same font as the logo

Colors

Designer to choose colors to be used in the design.

Requirements
Must have
• An upbeat vibe - the logo looks great so inline with that !
Should not have
• anything old fashioned and old style fonts

```html
<!DOCTYPE html>
<html lang="en">
<head>
<meta charset="utf-8">
<title>VORTEQ — Innovating Everyday Solutions</title>
<link href="https://fonts.googleapis.com/css2?family=Poppins:wght@400;500;600;700&display=swap" rel="stylesheet">
<style>
:root{
  --navy:#2f3b8f;
  --navy-dark:#2b3380;
  --cyan:#10aee0;
  --cyan-soft:#4fd3e0;
  --ink:#222;
  --panel:#f0f1f6;
  --footer:#1e2022;
  --white:#fff;
}
*{margin:0;padding:0;box-sizing:border-box}
html,body{width:1200px;height:2625px;overflow:hidden}
body{font-family:'Poppins',sans-serif;color:var(--ink);background:var(--white);position:relative}
.abs{position:absolute}

/* header */
.site-header{left:0;top:0;width:1200px;height:97px;background:var(--white)}
.brand{left:210px;top:32px;display:flex;align-items:center;gap:10px;font-weight:600;font-size:26px;letter-spacing:3px;color:var(--navy)}
.brand-dot{width:22px;height:22px;border-radius:50%;background:var(--cyan)}
.main-nav{left:460px;top:43px;display:flex;font-size:11.5px;font-weight:500;letter-spacing:.8px;color:#333}
.main-nav a{color:inherit;text-decoration:none;margin-right:58px}
.main-nav a.active{color:var(--cyan)}
.main-nav a:last-child{margin-right:0}

/* hero */
.hero{left:0;top:97px;width:1200px;height:613px;
  background:radial-gradient(ellipse at 30% 40%,#7fe3ec 0%,#2fbde0 35%,#1a8fd8 65%,#e9f3fb 100%)}
.hero-wave{left:40px;top:540px;width:1120px;height:140px;border-radius:50%;
  background:linear-gradient(90deg,rgba(30,140,230,.5),rgba(80,220,240,.6),rgba(255,255,255,0))}
.hero-art{left:680px;top:145px;width:420px;height:450px;border-radius:30px;
  background:radial-gradient(circle at 50% 50%,#3a78d8 0%,#7fd8f0 45%,#d8f3fa 100%);opacity:.9}
.hero-title{left:208px;top:228px;font-size:47px;line-height:54px;font-weight:700;color:var(--navy)}
.hero-sub{left:209px;top:367px;font-size:15px;font-weight:500;color:#1c2240}
.btn{display:flex;align-items:center;justify-content:center;border-radius:27px;color:var(--white);font-size:12px;font-weight:600;text-decoration:none}
.btn-navy{background:var(--navy-dark)}
.btn-cyan{background:var(--cyan)}
.hero-btn{left:209px;top:420px;width:157px;height:53px}

/* about */
.about-art{left:580px;top:738px;width:500px;height:342px;border-radius:20px;z-index:0;
  background:linear-gradient(180deg,#ffffff 0%,#e4e8ee 60%,#f6f7f9 100%)}
.about-title{left:209px;top:782px;font-size:31px;line-height:37px;font-weight:700;color:var(--navy);z-index:1}
.about-title .hl{color:var(--cyan)}
.about-text{left:210px;top:873px;width:340px;font-size:11.6px;line-height:18.8px;color:#2a2a2a;z-index:1}
.about-btn{left:210px;top:1020px;width:152px;height:54px;z-index:1}

/* products */
.products{left:0;top:1154px;width:1200px;height:576px;background:var(--panel)}
.section-title{width:1200px;left:0;text-align:center;font-size:31px;font-weight:700;color:var(--navy)}
.section-title .hl{color:var(--cyan)}
.tabs{left:209px;top:1255px;width:782px;height:50px;background:var(--white);border-radius:4px;
  box-shadow:0 3px 6px rgba(40,60,140,.08);display:flex;justify-content:center;gap:48px;
  font-size:11px;font-weight:500;color:#222;padding-top:18px}
.tabs span{height:32px}
.tabs .active{color:var(--cyan);border-bottom:2px solid var(--cyan)}
.product-art{left:210px;top:1330px;width:390px;height:300px;border-radius:20px;
  background:radial-gradient(circle at 55% 50%,#7fe6f2 0%,#dfe4ec 40%,#f0f1f6 80%)}
.product-name{left:626px;top:1336px;font-size:24px;font-weight:600;color:var(--cyan)}
.product-desc{left:626px;top:1381px;width:310px;font-size:11.6px;line-height:18.8px;color:#2a2a2a}
.features{left:626px;top:1463px;list-style:none;font-size:11.6px;font-weight:500;color:#1d1d1d}
.features li{display:flex;align-items:center;gap:14px;height:22.5px}
.features svg{width:11px;height:11px}
.product-btn{left:626px;top:1630px;width:152px;height:54px}

/* process */
.step{top:1840px;width:235px;height:272px;border-radius:8px;
  background:linear-gradient(160deg,#4fd3e0 0%,#1fb0dc 100%);text-align:center;color:var(--white)}
.step-icon{position:absolute;left:65px;top:26px;width:104px;height:104px;border-radius:50%;background:var(--white);display:flex;align-items:center;justify-content:center}
.step h3{position:absolute;top:148px;width:100%;font-size:16px;font-weight:600}
.step p{position:absolute;top:186px;left:14px;right:14px;font-size:11.4px;line-height:18.8px}

/* cta */
.cta{left:0;top:2187px;width:1200px;height:218px;
  background:radial-gradient(ellipse at 60% 60%,#8fe0ef 0%,#3fc3df 50%,#4fd3e0 100%)}
.cta-title{left:0;width:1200px;top:2240px;text-align:center;font-size:26px;font-weight:700;color:var(--white)}
.cta-btn{left:522px;top:2298px;width:157px;height:53px}

/* footer */
.site-footer{left:0;top:2405px;width:1200px;height:220px;background:var(--footer);color:var(--white)}
.site-footer .footer-brand{left:210px;top:43px;display:flex;align-items:center;gap:10px;font-size:26px;font-weight:600;letter-spacing:3px;color:var(--white)}
.site-footer .copyright{left:210px;top:110px;font-size:10.5px;color:var(--white)}
.footer-col{color:var(--white)}
.footer-col h4{font-size:15px;font-weight:600;margin-bottom:12px}
.footer-col p{font-size:10.5px;line-height:18.8px}
.socials{display:flex;gap:22px;margin-top:4px}
.socials span{width:14px;height:14px;border-radius:50%;background:var(--white)}
</style>
</head>
<body>

<header class="site-header abs">
  <div class="brand abs"><span class="brand-dot"></span>VORTEQ</div>
  <nav class="main-nav abs">
    <a class="active" href="#">HOME</a><a href="#">PRODUCTS</a><a href="#">FEATURES</a><a href="#">ABOUT US</a><a href="#">CONTACT US</a>
  </nav>
</header>

<section class="hero abs" role="img" aria-label="Blue swirling wave background"></section>
<div class="hero-wave abs"></div>
<div class="hero-art abs" role="img" aria-label="Translucent blue front-loading washing machine"></div>
<h1 class="hero-title abs">Innovating<br>Everyday Solutions</h1>
<p class="hero-sub abs">From cutting-edge home solutions to revolutionary</p>
<a class="btn btn-navy hero-btn abs" href="#">View Products</a>

<div class="about-art abs" role="img" aria-label="Hanger stand, compact washer and tall clothes dryer products"></div>
<h2 class="about-title abs">We bring<br><span class="hl">smart ideas</span> to life</h2>
<p class="about-text abs">At VORTEQ, we design with purpose. Our mission is to improve daily living through simple, clever, and beautifully engineered solutions.What starts as a spark of curiosity becomes a thoughtful product — whether it’s a reimagined hanger, a compact clothes dryer, or a pet treat innovation currently in patent development.</p>
<a class="btn btn-cyan about-btn abs" href="#">Learn More</a>

<section class="products abs"></section>
<h2 class="section-title abs" style="top:1194px">Our <span class="hl">Products</span></h2>
<div class="tabs abs">
  <span>LAUNDRY MARKET</span><span>HANGER ACCESSORY</span><span>MODERN CLOTHES DRYER</span><span class="active">PET TREAT DISPENSER</span>
</div>
<div class="product-art abs" role="img" aria-label="White round pet treat dispenser with glowing ring and treat bowl"></div>
<h3 class="product-name abs">Pet Treat Dispenser</h3>
<p class="product-desc abs">Smart, Automatic, and Pet-Friendly! The VORTEQ is an intelligent pet treat dispenser that makes snack time easier, healthier, and more fun for your furry friend.</p>
<ul class="features abs">
  <li><svg viewBox="0 0 12 12"><circle cx="6" cy="6" r="6" fill="#10aee0"/><path d="M3.3 6.2l1.8 1.8 3.6-3.6" stroke="#fff" stroke-width="1.5" fill="none"/></svg>Smart Dispensing Technology</li>
  <li><svg viewBox="0 0 12 12"><circle cx="6" cy="6" r="6" fill="#10aee0"/><path d="M3.3 6.2l1.8 1.8 3.6-3.6" stroke="#fff" stroke-width="1.5" fill="none"/></svg>App-Controlled Convenience</li>
  <li><svg viewBox="0 0 12 12"><circle cx="6" cy="6" r="6" fill="#10aee0"/><path d="M3.3 6.2l1.8 1.8 3.6-3.6" stroke="#fff" stroke-width="1.5" fill="none"/></svg>Voice &amp; Motion Activation</li>
  <li><svg viewBox="0 0 12 12"><circle cx="6" cy="6" r="6" fill="#10aee0"/><path d="M3.3 6.2l1.8 1.8 3.6-3.6" stroke="#fff" stroke-width="1.5" fill="none"/></svg>Customizable Portions</li>
  <li><svg viewBox="0 0 12 12"><circle cx="6" cy="6" r="6" fill="#10aee0"/><path d="M3.3 6.2l1.8 1.8 3.6-3.6" stroke="#fff" stroke-width="1.5" fill="none"/></svg>Rechargeable &amp; Eco-Friendly</li>
  <li><svg viewBox="0 0 12 12"><circle cx="6" cy="6" r="6" fill="#10aee0"/><path d="M3.3 6.2l1.8 1.8 3.6-3.6" stroke="#fff" stroke-width="1.5" fill="none"/></svg>Pet-Safe Materials</li>
</ul>
<a class="btn btn-cyan product-btn abs" href="#">Learn More</a>

<h2 class="section-title abs" style="top:1768px">How <span class="hl">We Build</span></h2>
<div class="step abs" style="left:206px">
  <div class="step-icon"><svg width="34" height="46" viewBox="0 0 34 46"><path d="M17 2a15 15 0 0 0-9 27c2 1.6 3 3.5 3 5.5h12c0-2 1-3.9 3-5.5A15 15 0 0 0 17 2z" fill="#10aee0"/><rect x="11" y="37" width="12" height="3" rx="1.5" fill="#10aee0"/><rect x="13" y="42" width="8" height="3" rx="1.5" fill="#10aee0"/></svg></div>
  <h3>Imagine It</h3>
  <p>We observe everyday problems and imagine practical, modern solutions with real impact.</p>
</div>
<div class="step abs" style="left:483px">
  <div class="step-icon"><svg width="48" height="48" viewBox="0 0 48 48"><path d="M8 40L30 18" stroke="#10aee0" stroke-width="7" stroke-linecap="round"/><circle cx="34" cy="14" r="9" fill="#10aee0"/><circle cx="38" cy="10" r="4" fill="#fff"/><path d="M10 10l28 28" stroke="#10aee0" stroke-width="6" stroke-linecap="round"/><rect x="4" y="4" width="10" height="10" rx="2" fill="#10aee0" transform="rotate(45 9 9)"/></svg></div>
  <h3>Design &amp; Build It</h3>
  <p>Using a mix of creativity and precision, we prototype, refine, and engineer every product with care.</p>
</div>
<div class="step abs" style="left:754px">
  <div class="step-icon"><svg width="46" height="46" viewBox="0 0 46 46"><path d="M42 4c-12 0-20 6-26 16l10 10c10-6 16-14 16-26z" fill="#10aee0"/><circle cx="31" cy="15" r="4" fill="#fff"/><path d="M16 20l-9 1-4 7 9-1zM26 30l-1 9-7 4 1-9z" fill="#10aee0"/><path d="M12 30l-6 10 10-6z" fill="#10aee0"/></svg></div>
  <h3>Launch &amp; Evolve</h3>
  <p>We test, launch, and continue to improve — creating products that people actually want</p>
</div>

<section class="cta abs" role="img" aria-label="Soft cyan abstract background"></section>
<h2 class="cta-title abs">Have a product idea? Let’s build it together.</h2>
<a class="btn btn-navy cta-btn abs" href="#">Start a Project</a>

<footer class="site-footer abs">
  <div class="footer-brand abs"><span class="brand-dot"></span>VORTEQ</div>
  <p class="copyright abs">© 2025 VORTEQ. All Rights Reserved.</p>
  <div class="footer-col abs" style="left:478px;top:47px">
    <h4>Quick Links</h4>
    <p>Home<br>About<br>Products<br>Contact<br>Support</p>
  </div>
  <div class="footer-col abs" style="left:634px;top:47px">
    <h4>Get in Touch</h4>
    <p>48 Brightwell Avenue, Unit 12<br>Harbor Point, CA 90311, USA<br>hello@vorteq.com<br>+1 (555) 310-2288</p>
  </div>
  <div class="footer-col abs" style="left:871px;top:47px">
    <h4>Follow Us</h4>
    <div class="socials"><span></span><span></span><span></span><span></span></div>
  </div>
</footer>

</body>
</html>
```